KW Holdings ltd*

I need a full website designed for for a 10,000m2 strorage facity which specialize in heavy commercial storage

it needs to be in english please

Target Market(s)

Comercial sector

Industry/Entity Type

Construction Company

Logo Text

KW

Coding

Coded - Design and coding required

Number of Pages Required

1 page

Font styles to use
Sans Serif

Colors
ec1f27
ffffff

Requirements
Must have
• Tel 0064 218846507
• email- liam@kwholdings.co.nz
Nice to have
• We specilize in large items with the facilty have 3 15tonne Gantry cranes and heavy mobile lifting equipment we can store items up to 20 tonne and we are fully covered and secure.
• square meter rates from 20m2 to 10,000 m2

```html
<!DOCTYPE html>
<html lang="en">
<head>
<meta charset="utf-8">
<title>KW Holdings ltd — Heavy Commercial Storage</title>
<link rel="stylesheet" href="https://fonts.googleapis.com/css2?family=Montserrat:wght@600;700;800;900&family=Poppins:wght@300;400;500&display=swap">
<style>
:root{
  --red:#ec1f27;
  --white:#ffffff;
  --ink:#1b1b1d;
  --muted:#555459;
  --board:#f5f5f5;
  --panel:#f0f0f0;
  --line:#b9b9bd;
  --footer:#1e1e1f;
  --footer-text:#c9c9cc;
  --head:'Montserrat',sans-serif;
  --body:'Poppins',sans-serif;
}
*{box-sizing:border-box;margin:0;padding:0}
html,body{width:1200px;height:2863px;overflow:hidden}
body{background:radial-gradient(ellipse at 50% 20%,#fbfbfb 0%,var(--board) 60%,#efefef 100%);font-family:var(--body);color:var(--ink);position:relative}

.board-brand{position:absolute;left:0;top:150px;width:1200px;text-align:center;font-family:var(--head);font-weight:800;font-size:46px;letter-spacing:7px;color:var(--ink)}

.divider{position:absolute;top:954px;left:374px;width:452px;height:8px}
.divider::before,.divider::after{content:"";position:absolute;top:4px;height:1px;width:203px;background:#4a4a50}
.divider::before{left:0}.divider::after{right:0}
.divider span{position:absolute;left:221px;top:0;width:9px;height:9px;border-radius:50%;background:var(--ink)}

.site{position:absolute;background:var(--white);overflow:hidden}
.site-header{position:relative;background:var(--white)}
.brand{position:absolute;font-family:var(--head);font-weight:800;color:var(--red);letter-spacing:1px;white-space:nowrap;transform:translateX(-50%)}
.contact-chip{position:absolute;display:flex;align-items:center;gap:8px;font-size:8px;letter-spacing:1px;color:var(--red);font-weight:300}
.icon-ring{width:22px;height:22px;border:1px solid var(--red);border-radius:50%;display:flex;align-items:center;justify-content:center}
.main-nav{position:relative;background:var(--red);height:32px}
.main-nav a{position:absolute;top:0;line-height:32px;transform:translateX(-50%);font-family:var(--head);font-weight:700;font-size:7.5px;letter-spacing:1px;color:var(--white);text-decoration:none;white-space:nowrap}
.main-nav a.current{color:var(--ink)}
.main-nav a.current::after{content:"";position:absolute;left:0;right:0;bottom:6px;height:1px;background:var(--ink)}

.hero{position:relative;height:324px;color:var(--white);text-align:center}
.hero-photo{position:absolute;inset:0;background:linear-gradient(180deg,#4b4a55 0%,#5c6480 35%,#3f4b6d 60%,#534c4e 85%,#3c3b45 100%)}
.hero-title{position:absolute;left:0;right:0;top:84px;font-family:var(--head);font-weight:900;font-size:21.5px;line-height:35px;letter-spacing:2px;text-shadow:0 1px 2px rgba(0,0,0,.3)}
.hero-text{position:absolute;left:100px;right:100px;top:183px;font-size:14.5px;line-height:17.5px;letter-spacing:1.2px;font-weight:400}
.btn{display:inline-block;background:var(--red);color:var(--white);font-size:8px;letter-spacing:.8px;font-weight:400;text-align:center}
.hero .btn{position:absolute;left:50%;top:246px;width:81px;height:24px;line-height:24px;transform:translateX(-50%)}
.hero-arrow{position:absolute;top:150px;width:28px;height:28px;border:1.5px solid var(--red);border-radius:50%;display:flex;align-items:center;justify-content:center}

.photo{display:block}
.photo-warehouse{background:linear-gradient(180deg,#3b4660 0%,#7d8aa8 45%,#4a5877 75%,#2f3a52 100%)}
.photo-team{background:linear-gradient(180deg,#56607a 0%,#3a4460 50%,#262d40 100%)}
.photo-forklift{background:linear-gradient(160deg,#6d7186 0%,#9b8c4a 45%,#c9a72e 55%,#4d5368 100%)}

.section-title{font-family:var(--head);font-weight:800;color:var(--ink);text-align:center;letter-spacing:2px}
.lead{text-align:center;color:var(--muted);font-weight:300}
.link-more{color:var(--red);font-weight:300;white-space:nowrap}

.desktop{left:371px;top:1044px;width:716px;height:1628px}
.desktop .site-header{height:63px}
.desktop .brand{left:116px;top:24px;font-size:12px}
.services{position:relative;height:502px;background:var(--white)}
.services .section-title{position:absolute;left:0;right:0;top:58px;font-size:20px}
.services .lead{position:absolute;left:150px;right:150px;top:99px;font-size:8px;line-height:13px;letter-spacing:.5px}
.service-card{position:absolute;top:150px;width:167px}
.service-card .photo{height:118px}
.service-card h3{margin-top:22px;font-family:var(--head);font-weight:800;font-size:13.5px;line-height:24px;letter-spacing:1.2px;height:60px;white-space:nowrap}
.service-card p{font-size:8px;line-height:13.5px;letter-spacing:.5px;color:var(--muted);font-weight:300}
.service-card .link-more{display:block;margin-top:17px;font-size:8px;letter-spacing:.5px}
.contact{position:relative;height:481px;background:var(--panel)}
.contact .section-title{position:absolute;left:0;right:0;top:55px;font-size:20px;line-height:33px}
.contact .lead{position:absolute;left:150px;right:150px;top:134px;font-size:8px;line-height:13px;letter-spacing:.5px}
.field{position:absolute;border:1px solid var(--line);background:var(--panel);font-size:8px;letter-spacing:.6px;color:#7b7b80;font-weight:300;padding:0 15px;line-height:32px}
.contact .btn{position:absolute;left:50%;top:393px;transform:translateX(-50%);width:97px;height:26px;line-height:26px}
.site-footer{position:relative;background:var(--footer);color:var(--footer-text)}
.desktop .site-footer{height:224px}
.footer-col{position:absolute;top:50px}
.footer-col h4{font-family:var(--head);font-weight:600;font-size:10.5px;letter-spacing:1.5px;color:var(--white);margin-bottom:20px}
.footer-col li{list-style:none;font-size:7.5px;letter-spacing:.8px;line-height:19px;font-weight:300}
.footer-legal{position:absolute;top:204px;font-size:7.5px;letter-spacing:.8px;font-weight:300}

.screen-wide{left:241px;top:346px;width:716px;height:445px}
.screen-wide .site-header{height:72px}
.screen-wide .brand{left:116px;top:29px;font-size:12px}
.screen-wide .main-nav{height:31px}
.screen-wide .main-nav a{line-height:31px}

.screen-narrow{left:861px;top:511px;width:163px;height:361px;border-radius:10px;box-shadow:0 8px 24px rgba(0,0,0,.12)}
.screen-narrow .link-more{position:absolute;left:0;right:0;text-align:center;font-size:6.5px}
.screen-narrow .photo{position:absolute;left:13px;top:60px;width:139px;height:98px}
.screen-narrow h3{position:absolute;left:0;right:0;top:174px;text-align:center;font-family:var(--head);font-weight:800;font-size:7.5px;letter-spacing:.8px}
.screen-narrow p{position:absolute;left:16px;right:16px;top:201px;text-align:center;font-size:7.8px;line-height:11px;color:var(--muted);font-weight:300}
.screen-narrow .band{position:absolute;left:0;right:0;bottom:0;height:45px;background:var(--panel)}
.screen-narrow .band span{position:absolute;left:0;right:0;bottom:8px;text-align:center;font-family:var(--head);font-weight:800;font-size:7.5px;letter-spacing:.6px}

.mobile{left:112px;top:1044px;width:168px;height:1758px}
.mobile .site-header{height:28px}
.mobile .brand{left:84px;top:9px;font-size:6px}
.burger{position:absolute;left:9px;top:11px;width:8px;height:6px;border-top:1px solid var(--ink);border-bottom:1px solid var(--ink)}
.burger::after{content:"";position:absolute;left:0;right:0;top:1.5px;height:1px;background:var(--ink)}
.mini-ring{position:absolute;top:9px;width:8px;height:8px;border:.8px solid var(--red);border-radius:50%}
.mobile .hero{height:253px}
.mobile .hero-title{top:52px;left:18px;right:18px;font-size:9px;line-height:14.5px;letter-spacing:.8px}
.mobile .hero-text{top:124px;left:18px;right:18px;font-size:7px;line-height:8.8px;letter-spacing:.4px}
.mobile .hero .btn{top:187px;width:58px;height:18px;line-height:18px;font-size:6px}
.mobile .hero-arrow{top:222px;width:14px;height:14px;border-width:1px}
.m{position:absolute;left:0;right:0;text-align:center}
.m-title{font-family:var(--head);font-weight:800;font-size:7.5px;letter-spacing:.7px}
.m-text{left:18px;right:18px;font-size:6.3px;line-height:9px;color:var(--muted);font-weight:300}
.m-card-text{left:18px;right:18px;font-size:8.2px;line-height:11px;color:var(--muted);font-weight:300}
.m-link{font-size:6.3px;color:var(--red);font-weight:300}
.m-photo{position:absolute;left:15px;width:138px;height:98px}
.m-contact{position:absolute;left:0;right:0;top:1144px;height:350px;background:var(--panel)}
.m-field{position:absolute;left:18px;width:133px;height:17px;border:1px solid var(--line);font-size:5.5px;color:#7b7b80;line-height:15px;padding:0 8px;font-weight:300;background:var(--panel)}
.mobile .site-footer{position:absolute;left:0;right:0;top:1494px;height:264px}
.mf-head{position:absolute;font-family:var(--head);font-weight:700;font-size:6.5px;letter-spacing:.6px;color:var(--white)}
.mf-list{position:absolute;list-style:none;font-size:5.5px;line-height:12px;font-weight:300}
.mobile .site-footer .brand{left:128px;top:170px;font-size:6px;letter-spacing:.5px}
</style>
</head>
<body>

<div class="board-brand">KW HOLDINGS</div>

<section class="site screen-wide" aria-label="Desktop view of the homepage top">
  <header class="site-header">
    <span class="brand">KW HOLDINGS</span>
    <div class="contact-chip" style="left:350px;top:25px">
      <span class="icon-ring"><svg width="10" height="10" viewBox="0 0 24 24"><path d="M6.6 10.8a15.2 15.2 0 0 0 6.6 6.6l2.2-2.2c.3-.3.7-.4 1-.2 1.1.4 2.3.6 3.6.6.6 0 1 .4 1 1V20c0 .6-.4 1-1 1A17 17 0 0 1 3 4c0-.6.4-1 1-1h3.5c.6 0 1 .4 1 1 0 1.3.2 2.5.6 3.6.1.3 0 .7-.2 1z" fill="#ec1f27"/></svg></span>0064-218-846507</div>
    <div class="contact-chip" style="left:493px;top:25px">
      <span class="icon-ring"><svg width="10" height="10" viewBox="0 0 24 24"><path d="M3 5h18v14H3z" fill="#ec1f27"/><path d="M3 5l9 7 9-7" fill="none" stroke="#fff" stroke-width="2"/></svg></span>liam@kwholdings.co.nz</div>
  </header>
  <nav class="main-nav">
    <a class="current" style="left:159px">HOME</a>
    <a style="left:286px">WARE HOUSE STORAGE</a>
    <a style="left:426px">ABOUTS US</a>
    <a style="left:542px">CONTACT US</a>
  </nav>
  <div class="hero">
    <div class="hero-photo" role="img" aria-label="Interior of a large industrial warehouse with gantry cranes"></div>
    <h1 class="hero-title">WE SPECILIZE IN LARGE ITEMS WITH THE<br>FACILTY HAVE 3 15TONNE GANTRY CRANE</h1>
    <p class="hero-text">Heavy mobile lifting equipment we can store items up to 20 tonne and we are fully covered and secure. square meter rates from 20m2 to 10,000 m2</p>
    <span class="btn">Read More</span>
    <span class="hero-arrow" style="left:42px"><svg width="10" height="10" viewBox="0 0 10 10"><path d="M6.5 1.5L3 5l3.5 3.5" fill="none" stroke="#ec1f27" stroke-width="1.2"/></svg></span>
  </div>
</section>

<section class="site screen-narrow" aria-label="Mobile view of a service card">
  <span class="link-more" style="top:33px">Trust in Experience →</span>
  <div class="photo photo-forklift" role="img" aria-label="Forklift operator moving stock in a warehouse"></div>
  <h3>RELIABLE TRANSPORTATION</h3>
  <p>Lorem ipsum dolor sit amet, consectetur adipiscing elit, sed do eiusmod tempor incididunt ut labore et dolore magna aliqua.</p>
  <span class="link-more" style="top:274px">Create Business Solution →</span>
  <div class="band"><span>CONTACT US FOR MORE DETAIL</span></div>
</section>

<div class="divider"><span></span></div>

<section class="site mobile" aria-label="Mobile homepage">
  <header class="site-header">
    <span class="burger"></span>
    <span class="brand">KW HOLDINGS</span>
    <span class="mini-ring" style="left:139px"></span>
    <span class="mini-ring" style="left:151px"></span>
  </header>
  <div class="hero">
    <div class="hero-photo" role="img" aria-label="Interior of a large industrial warehouse with gantry cranes"></div>
    <h1 class="hero-title">WE SPECILIZE IN LARGE ITEMS WITH THE FACILTY HAVE 3 15TONNE GANTRY CRANES</h1>
    <p class="hero-text">Heavy mobile lifting equipment we can store items up to 20 tonne and we are fully covered and secure. square meter rates from 20m2 to 10,000 m2</p>
    <span class="btn">Read More</span>
    <span class="hero-arrow" style="left:8px"></span>
    <span class="hero-arrow" style="left:146px"></span>
  </div>

  <h2 class="m m-title" style="top:312px">KW STORAGE SERVICES</h2>
  <p class="m m-text" style="top:339px">Lorem ipsum dolor sit amet, consectetur adipiscing elit, sed do eiusmod tempor incididunt ut labore et dolore magna aliqua.</p>

  <div class="m-photo photo-warehouse" style="top:406px" role="img" aria-label="Empty warehouse floor with racking"></div>
  <h3 class="m m-title" style="top:523px">NEED WAREHOUSE SPACE</h3>
  <p class="m m-card-text" style="top:549px">Lorem ipsum dolor sit amet, consectetur adipiscing elit, sed do eiusmod tempor incididunt ut labore et dolore magna aliqua.</p>
  <span class="m m-link" style="top:622px">Check Availability Today →</span>

  <div class="m-photo photo-team" style="top:648px" role="img" aria-label="Staff member checking a tablet among shelving"></div>
  <h3 class="m m-title" style="top:765px">YOUR OWN HANDLING TEAM</h3>
  <p class="m m-card-text" style="top:791px">Lorem ipsum dolor sit amet, consectetur adipiscing elit, sed do eiusmod tempor incididunt ut labore et dolore magna aliqua.</p>
  <span class="m m-link" style="top:864px">Trust in Experience →</span>

  <div class="m-photo photo-forklift" style="top:890px" role="img" aria-label="Forklift operator moving stock in a warehouse"></div>
  <h3 class="m m-title" style="top:1007px">RELIABLE TRANSPORTATION</h3>
  <p class="m m-card-text" style="top:1033px">Lorem ipsum dolor sit amet, consectetur adipiscing elit, sed do eiusmod tempor incididunt ut labore et dolore magna aliqua.</p>
  <span class="m m-link" style="top:1105px">Create Business Solution →</span>

  <div class="m-contact">
    <h2 class="m m-title" style="top:34px">CONTACT US FOR MORE DETAIL</h2>
    <p class="m m-text" style="top:60px">Lorem ipsum dolor sit amet, consectetur adipiscing elit, sed do eiusmod tempor incididunt ut labore et dolore magna aliqua.</p>
    <div class="m-field" style="top:126px">First Name:</div>
    <div class="m-field" style="top:150px">Last Name:</div>
    <div class="m-field" style="top:175px">Email:</div>
    <div class="m-field" style="top:200px">Phone Number:</div>
    <div class="m-field" style="top:224px;height:62px">Message:</div>
    <span class="btn" style="position:absolute;left:48px;top:296px;width:73px;height:19px;line-height:19px;font-size:6px">Send Message</span>
  </div>

  <footer class="site-footer">
    <h4 class="mf-head" style="left:9px;top:24px">QUICK LINKS</h4>
    <ul class="mf-list" style="left:9px;top:44px"><li>Home</li><li>Ware House Storage</li><li>Abouts Us</li><li>Contact Us</li><li>More Info</li></ul>
    <h4 class="mf-head" style="left:113px;top:24px">OTHERS</h4>
    <ul class="mf-list" style="left:113px;top:44px"><li>Dummy</li><li>Ware House</li><li>Lorem</li><li>FAQs</li><li>KW Holdings</li></ul>
    <h4 class="mf-head" style="left:9px;top:122px">QUICK LINKS</h4>
    <ul class="mf-list" style="left:9px;top:142px"><li>EMAIL ADDRESS</li><li>liam@kwholdings.co.nz</li><li style="margin-top:6px">PHONE</li><li>0064-218-846507</li></ul>
    <span class="brand">KW HOLDINGS</span>
    <span class="mf-list" style="left:9px;top:227px">Privacy &amp; Policy</span>
    <span class="mf-list" style="left:9px;top:243px">©2020. KW Holdings ltd</span>
  </footer>
</section>

<main class="site desktop" aria-label="Desktop homepage">
  <header class="site-header">
    <span class="brand">KW HOLDINGS</span>
    <div class="contact-chip" style="left:349px;top:21px">
      <span class="icon-ring"><svg width="10" height="10" viewBox="0 0 24 24"><path d="M6.6 10.8a15.2 15.2 0 0 0 6.6 6.6l2.2-2.2c.3-.3.7-.4 1-.2 1.1.4 2.3.6 3.6.6.6 0 1 .4 1 1V20c0 .6-.4 1-1 1A17 17 0 0 1 3 4c0-.6.4-1 1-1h3.5c.6 0 1 .4 1 1 0 1.3.2 2.5.6 3.6.1.3 0 .7-.2 1z" fill="#ec1f27"/></svg></span>0064-218-846507</div>
    <div class="contact-chip" style="left:492px;top:21px">
      <span class="icon-ring"><svg width="10" height="10" viewBox="0 0 24 24"><path d="M3 5h18v14H3z" fill="#ec1f27"/><path d="M3 5l9 7 9-7" fill="none" stroke="#fff" stroke-width="2"/></svg></span>liam@kwholdings.co.nz</div>
  </header>
  <nav class="main-nav">
    <a class="current" style="left:159px">HOME</a>
    <a style="left:286px">WARE HOUSE STORAGE</a>
    <a style="left:426px">ABOUTS US</a>
    <a style="left:542px">CONTACT US</a>
  </nav>
  <div class="hero">
    <div class="hero-photo" role="img" aria-label="Interior of a large industrial warehouse with gantry cranes"></div>
    <h1 class="hero-title">WE SPECILIZE IN LARGE ITEMS WITH THE<br>FACILTY HAVE 3 15TONNE GANTRY CRANES</h1>
    <p class="hero-text">Heavy mobile lifting equipment we can store items up to 20 tonne and we are fully covered and secure. square meter rates from 20m2 to 10,000 m2</p>
    <span class="btn">Read More</span>
    <span class="hero-arrow" style="left:42px"><svg width="10" height="10" viewBox="0 0 10 10"><path d="M6.5 1.5L3 5l3.5 3.5" fill="none" stroke="#ec1f27" stroke-width="1.2"/></svg></span>
    <span class="hero-arrow" style="left:645px"><svg width="10" height="10" viewBox="0 0 10 10"><path d="M3.5 1.5L7 5 3.5 8.5" fill="none" stroke="#ec1f27" stroke-width="1.2"/></svg></span>
  </div>

  <section class="services">
    <h2 class="section-title">KW STORAGE SERVICES</h2>
    <p class="lead">Lorem ipsum dolor sit amet, consectetur adipiscing elit, sed do eiusmod tempor incididunt ut labore et dolore magna aliqua.</p>
    <article class="service-card" style="left:90px">
      <div class="photo photo-warehouse" role="img" aria-label="Empty warehouse floor with racking"></div>
      <h3>NEED WAREHOUSE<br>SPACE</h3>
      <p>Lorem ipsum dolor sit amet, consectetur adipiscing elit, sed do eiusmod tempor incididunt ut labore et dolore magna aliqua.</p>
      <span class="link-more">Check Availability Today &nbsp;⟶</span>
    </article>
    <article class="service-card" style="left:275px">
      <div class="photo photo-team" role="img" aria-label="Staff member checking a tablet among shelving"></div>
      <h3>YOUR OWN<br>HANDLING TEAM</h3>
      <p>Lorem ipsum dolor sit amet, consectetur adipiscing elit, sed do eiusmod tempor incididunt ut labore et dolore magna aliqua.</p>
      <span class="link-more">Trust in Experience &nbsp;⟶</span>
    </article>
    <article class="service-card" style="left:459px">
      <div class="photo photo-forklift" role="img" aria-label="Forklift operator moving stock in a warehouse"></div>
      <h3>RELIABLE<br>TRANSPORTATION</h3>
      <p>Lorem ipsum dolor sit amet, consectetur adipiscing elit, sed do eiusmod tempor incididunt ut labore et dolore magna aliqua.</p>
      <span class="link-more">Creating Business Solution &nbsp;⟶</span>
    </article>
  </section>

  <section class="contact">
    <h2 class="section-title">CONTACT US FOR MORE<br>DETAILS</h2>
    <p class="lead">Lorem ipsum dolor sit amet, consectetur adipiscing elit, sed do eiusmod tempor incididunt ut labore et dolore magna aliqua.</p>
    <div class="field" style="left:123px;top:188px;width:224px;height:33px">First Name:</div>
    <div class="field" style="left:369px;top:188px;width:224px;height:33px">Last Name:</div>
    <div class="field" style="left:123px;top:237px;width:224px;height:33px">Email Address:</div>
    <div class="field" style="left:369px;top:237px;width:224px;height:33px">Phone Number:</div>
    <div class="field" style="left:123px;top:286px;width:470px;height:79px">Messages:</div>
    <span class="btn">Send Message</span>
  </section>

  <footer class="site-footer">
    <span class="brand" style="left:140px;top:105px;font-size:15px">KW HOLDINGS</span>
    <div class="footer-col" style="left:257px"><h4>QUICK LINKS</h4><ul><li>Home</li><li>Ware House Storage</li><li>Abouts Us</li><li>Contact Us</li><li>More Info</li></ul></div>
    <div class="footer-col" style="left:377px"><h4>OTHERS</h4><ul><li>Dummy</li><li>Ware House</li><li>Lorem</li><li>FAQs</li><li>KW Holdings</li></ul></div>
    <div class="footer-col" style="left:497px"><h4>CONTACT</h4><ul><li>EMAIL ADDRESS</li><li>liam@kwholdings.co.nz</li><li style="margin-top:6px">PHONE</li><li>0064-218-846507</li></ul></div>
    <span class="footer-legal" style="left:90px">Privacy &amp; Policy</span>
    <span class="footer-legal" style="right:90px">©2020. KW Holdings ltd</span>
  </footer>
</main>

</body>
</html>
```